Schlichtes Design für Malerbetrieb
Zielgruppe
Wir sind ein mittelgroßer Malerbetrieb in München mit umfangreichem Leistungsspektrum.
Unsere Hauptleistungen sind: Fassadenrenovierung, Altbausanierung, Betoninstandsetzung, Balkonabdichtung (kein Neubau!).
Unsere Zielgruppen sind: Hausverwaltungen, Firmen und Privatpersonen.
Unsere Kunden schätzen: Konstruktive Organisation und Planung im Vorfeld, Zuverlässigkeit, saubere Arbeitsweise, dauerhafte Balkonabdichtungen.
Aufgabenstellung
Wir möchten eine langlebige, stilvolle, minimalistische Homepage.
Wir möchten von der bestehenden Homepage nur die Schriftart für unseren Firmennamen (Century Gothic) und wenn möglich (nicht zwingend), irgendwo das florale Muster einbauen. Corporate-Design haben wir nicht.
Farbtöne: Firmennamen Orange (hellorange bis erdiges Orange möglich, da sind wir nicht fixiert) , einen dunklen Hintergrundfarbton (Petrol-Blaugrau ?) mit gelbem (neon bis senfgelb) Akzent (Linien), Blumenmuster weiß, grau.
Dies sind nur unsere Ideen. Wir sind aber auch absolut offen für eure Profi-Ideen.
Wir möchten uns von den unzähligen langweiligen 'Pinselseiten mit veralteten Bilder' unserer Kollegen interessant und mit Stil abheben.
Eher nach dem Motto 'weniger ist mehr'.
Einen positiven, sympathischen Eindruck geben und unsere Leistungen in den Vordergrund bringen.
Da wir viele Stammkunden haben, betreiben wir kein Social-Media und möchten dies vorerst auch nicht tun.
Die Seite wird in den nächsten Jahren nicht verändert, höchstens die Bilder aktualisiert.
Die Texte haben wir alle selbst entworfen und möchten wir so übernehmen.
Die Galerien sollen unkompliziert anzuschauen sein.
Uns gefällt die Struktur und Schlichtheit von https://vaartmolen.nl/ oder Timbra.de gut und wir mögen Vintage-Grafiken gerne.
Einerseits darf die Seite geradlinig, andererseits aber auch rund und floral wirken.

```html
<!DOCTYPE html>
<html lang="de">
<head>
<meta charset="utf-8">
<title>kolbrit malerarbeiten – Start</title>
<link href="https://fonts.googleapis.com/css2?family=Questrial&family=Didact+Gothic&family=Fira+Sans:ital,wght@0,400;0,600;1,400;1,600&display=swap" rel="stylesheet">
<style>
  :root {
    --petrol: #233a47;
    --lime: #c8cf00;
    --page: #f4f4f4;
    --white: #ffffff;
    --text: #555a5e;
    --heading: #5c5c5c;
  }
  * { box-sizing: border-box; margin: 0; padding: 0; }
  html, body { width: 1200px; height: 2503px; overflow: hidden; }
  body { position: relative; background: var(--white); font-family: "Fira Sans", sans-serif; color: var(--text); }
  .abs { position: absolute; }

  /* Header */
  .site-header { left: 0; top: 0; width: 1200px; height: 108px; background: var(--petrol); }
  .brand { left: 172px; top: 22px; font-family: "Questrial", sans-serif; font-size: 40px; color: var(--lime); letter-spacing: 1px; line-height: 1; }
  .brand-sub { left: 266px; top: 65px; font-family: "Questrial", sans-serif; font-size: 11px; color: var(--lime); }
  .nav-active { left: 395px; top: 0; width: 84px; height: 70px; }
  .nav-item { top: 42px; font-size: 13px; font-weight: 600; font-style: italic; color: var(--lime); letter-spacing: .5px; text-transform: uppercase; }
  .nav-item.current { color: var(--petrol); }

  /* Hero */
  .hero { left: 0; top: 108px; width: 1200px; height: 305px; background: linear-gradient(180deg, #b8c3cb 0%, #d4d9dc 55%, #e2e2dd 100%); }
  .hero-title { left: 172px; top: 204px; font-family: "Didact Gothic", sans-serif; font-weight: 400; font-size: 60px; color: var(--white); line-height: 1; }
  .hero-sub { left: 173px; top: 277px; font-family: "Didact Gothic", sans-serif; font-size: 26px; color: var(--white); }

  /* Main */
  .main { left: 0; top: 413px; width: 1200px; height: 1618px; background: var(--page); overflow: hidden; }
  .ornament { left: 850px; top: 110px; width: 420px; height: 1050px;
    background:
      radial-gradient(ellipse 120px 90px at 250px 70px, rgba(218,218,218,.9), rgba(244,244,244,0) 100%),
      radial-gradient(ellipse 160px 260px at 290px 330px, rgba(222,222,222,.85), rgba(244,244,244,0) 100%),
      radial-gradient(ellipse 130px 200px at 250px 640px, rgba(220,220,220,.85), rgba(244,244,244,0) 100%),
      radial-gradient(ellipse 150px 180px at 300px 900px, rgba(224,224,224,.8), rgba(244,244,244,0) 100%); }
  .intro-title { left: 170px; top: 82px; font-family: "Didact Gothic", sans-serif; font-weight: 400; font-size: 60px; line-height: 68px; color: var(--heading); }
  .intro-title .accent { color: var(--lime); }
  .slide-dots { left: 572px; top: 130px; font-size: 12px; color: #e6e6e6; }
  .slide-dots span { display: inline-block; width: 22px; margin-right: 9px; text-align: center; border-bottom: 1px solid #e6e6e6; line-height: 15px; }
  .intro-text { left: 172px; top: 262px; width: 850px; font-size: 13.6px; line-height: 26px; }
  .slider { left: 171px; top: 396px; width: 858px; height: 463px; background: linear-gradient(180deg, #eef1f3 0%, #d7d4cf 45%, #5e4a3e 100%); }
  .slider-arrow { top: 586px; width: 43px; height: 84px; }
  .book-photo { left: 171px; top: 909px; width: 343px; height: 514px; background: linear-gradient(180deg, #d9dada 0%, #b9b8b6 40%, #d8633f 62%, #1f2f4a 80%, #15203a 100%); }
  .body-text { left: 566px; top: 915px; width: 462px; font-size: 13.6px; line-height: 25.7px; }
  .body-text p + p { margin-top: 25.7px; }
  .body-text p.tight { margin-top: 0; }
  .btn { top: 1481px; width: 178px; height: 50px; border-radius: 3px; font-family: "Fira Sans", sans-serif; font-weight: 600; font-size: 22px; display: flex; align-items: center; justify-content: center; }
  .btn-primary { left: 566px; background: var(--lime); color: var(--petrol); }
  .btn-dark { left: 762px; background: var(--petrol); color: var(--white); }

  /* Footer */
  .footer-mark { left: 157px; top: 2104px; width: 56px; height: 56px; border: 3px solid var(--lime); border-radius: 50%; }
  .footer-col { font-size: 14px; line-height: 26px; color: var(--text); }
  .footer-col h4 { font-weight: 400; color: var(--petrol); font-size: 14px; }
  .footer-col .gap { margin-top: 26px; }
  .footer-list { list-style: none; }
  .footer-list li { position: relative; padding-left: 21px; }
  .footer-list li svg { position: absolute; left: 0; top: 6px; }
  .footer-list li.multi { line-height: 17px; padding-top: 4px; padding-bottom: 9px; }
  .footer-list li.multi svg { top: 4px; }

  .bottom-bar { left: 0; top: 2365px; width: 1200px; height: 138px; background: var(--petrol); }
  .legal-links { left: 174px; top: 2408px; font-size: 14px; color: var(--lime); }
  .legal-links span + span { margin-left: 16px; }
  .copyright { left: 172px; top: 2441px; font-size: 14px; color: var(--lime); }
  .brand-bottom { left: 838px; top: 2408px; font-family: "Questrial", sans-serif; font-size: 44px; color: var(--lime); letter-spacing: 1px; line-height: 1; }
  .brand-bottom-sub { left: 923px; top: 2451px; font-family: "Questrial", sans-serif; font-size: 13px; color: var(--lime); }
</style>
</head>
<body>

<header class="site-header abs">
  <div class="brand abs">kolbrit</div>
  <div class="brand-sub abs">malerarbeiten</div>
  <svg class="nav-active abs" viewBox="0 0 84 70"><polygon points="19,0 84,0 70,70 0,70" fill="#c8cf00"/></svg>
  <nav>
    <span class="nav-item current abs" style="left:414px">Start</span>
    <span class="nav-item abs" style="left:492px">Leistungen</span>
    <span class="nav-item abs" style="left:620px">Portrait</span>
    <span class="nav-item abs" style="left:735px">Auszeichnung</span>
    <span class="nav-item abs" style="left:893px">Karriere</span>
    <span class="nav-item abs" style="left:1016px">Kontakt</span>
  </nav>
</header>

<section class="hero abs" role="img" aria-label="Heller Altbau-Innenraum mit weißen Säulen und Stuckdecke"></section>
<h1 class="hero-title abs">Malerarbeiten in Perfektion.</h1>
<p class="hero-sub abs">Qualität kennt keine Kompromisse. Professionelle Malerarbeiten</p>

<main class="main abs">
  <div class="ornament abs" role="img" aria-label="Großes florales Ornament in hellem Grau"></div>
  <h2 class="intro-title abs">Aus dem Chaos<br>zur <span class="accent">Ordnung.</span></h2>
  <div class="slide-dots abs"><span>1</span><span>2</span><span>3</span></div>
  <p class="intro-text abs">Nemo enim ipsam voluptatem quia voluptas sit aspernatur aut odit aut fugit, sed quia consequuntur magni dolores eos qui ratione voluptatem sequi nesciunt. Neque porro quisquam est, qui dolorem ipsum quia dolor sit amet, consectetur, adipisci velit, sed quia non numquam eius modi tempora incidunt ut labore et dolore magnam aliquam quaerat voluptatem.</p>

  <div class="slider abs" role="img" aria-label="Frisch renovierter Ladenraum mit Kleiderständern, Rundbogenfenstern und Holzboden"></div>
  <svg class="slider-arrow abs" style="left:162px" viewBox="0 0 43 84"><rect width="43" height="84" fill="#c8cf00"/><polyline points="25,33 17,42 25,51" fill="none" stroke="#fff" stroke-width="2"/></svg>
  <svg class="slider-arrow abs" style="left:994px" viewBox="0 0 43 84"><rect width="43" height="84" fill="#c8cf00"/><polyline points="18,33 26,42 18,51" fill="none" stroke="#fff" stroke-width="2"/></svg>

  <div class="book-photo abs" role="img" aria-label="Nahaufnahme eines Fachbuchs zu Maler- und Lackiererarbeiten"></div>
  <div class="body-text abs">
    <p>Lorem ipsum dolor sit amet, consectetur adipisicing elit, sed do eiusmod tempor incididunt ut labore et dolore magna aliqua. Ut enim ad minim veniam, quis nostrud exercitation ullamco laboris nisi ut aliquip ex ea commodo consequat. Duis aute irure dolor in reprehenderit in voluptate velit esse cillum dolore eu fugiat nulla pariatur. Excepteur sint occaecat cupidatat non proident, sunt in culpa qui officia deserunt mollit anim id est laborum.</p>
    <p>Sed ut perspiciatis unde omnis iste natus error sit voluptatem accusantium doloremque laudantium, totam rem aperiam, eaque ipsa quae ab illo inventore veritatis et quasi architecto beatae vitae dicta sunt explicabo.</p>
    <p class="tight">Nemo enim ipsam voluptatem quia voluptas sit aspernatur aut odit aut fugit, sed quia consequuntur magni dolores eos qui ratione voluptatem sequi nesciunt. Neque porro quisquam est, qui dolorem ipsum quia dolor sit amet, consectetur, adipisci velit, sed quia non numquam eius modi tempora incidunt ut labore et dolore magnam aliquam quaerat voluptatem.</p>
  </div>

  <a class="btn btn-primary abs">Kontakt</a>
  <a class="btn btn-dark abs">Portrait</a>
</main>

<footer>
  <div class="footer-mark abs"></div>

  <div class="footer-col abs" style="left:168px; top:2190px">
    <h4>Kontakt</h4>
    <ul class="footer-list">
      <li><svg width="14" height="14" viewBox="0 0 14 14"><polyline points="2,7 6,11 12,3" fill="none" stroke="#c8cf00" stroke-width="2.4"/></svg>Telefon: 089514270</li>
      <li><svg width="14" height="14" viewBox="0 0 14 14"><polyline points="2,7 6,11 12,3" fill="none" stroke="#c8cf00" stroke-width="2.4"/></svg>Telefax: 089514271</li>
      <li><svg width="14" height="14" viewBox="0 0 14 14"><polyline points="2,7 6,11 12,3" fill="none" stroke="#c8cf00" stroke-width="2.4"/></svg>info@kolbrit-gmbh.de</li>
    </ul>
  </div>

  <div class="footer-col abs" style="left:420px; top:2112px">
    <h4>Büro</h4>
    <p>Lindenhangstr. 7</p>
    <p>82031 Grünfeld</p>
    <h4 class="gap">Werkstatt</h4>
    <p>Sägewerkstr. 32b</p>
    <p>81369 München</p>
  </div>

  <div class="footer-col abs" style="left:672px; top:2113px">
    <h4>Links</h4>
    <ul class="footer-list">
      <li><svg width="14" height="14" viewBox="0 0 14 14"><polyline points="2,7 6,11 12,3" fill="none" stroke="#c8cf00" stroke-width="2.4"/></svg>berufklar | Berufe entdecken online!</li>
      <li><svg width="14" height="14" viewBox="0 0 14 14"><polyline points="2,7 6,11 12,3" fill="none" stroke="#c8cf00" stroke-width="2.4"/></svg>Handwerksforum für Südbayern und das Umland</li>
      <li><svg width="14" height="14" viewBox="0 0 14 14"><polyline points="2,7 6,11 12,3" fill="none" stroke="#c8cf00" stroke-width="2.4"/></svg>Maler- und Lackierer Verbund Isartal</li>
      <li class="multi"><svg width="14" height="14" viewBox="0 0 14 14"><polyline points="2,7 6,11 12,3" fill="none" stroke="#c8cf00" stroke-width="2.4"/></svg>Initiative Nachwuchs für nationale und<br>internationale Berufswettbewerbe</li>
      <li><svg width="14" height="14" viewBox="0 0 14 14"><polyline points="2,7 6,11 12,3" fill="none" stroke="#c8cf00" stroke-width="2.4"/></svg>Webseite des internationalen Handwerkswettbewerbs</li>
    </ul>
  </div>

  <div class="bottom-bar abs"></div>
  <div class="legal-links abs"><span>Datenschutz</span><span>Impressum</span></div>
  <p class="copyright abs">Copyright © 1996-2016 Kolbrit Malerarbeiten GmbH. Alle Rechte vorbehalten.</p>
  <div class="brand-bottom abs">kolbrit</div>
  <div class="brand-bottom-sub abs">malerarbeiten</div>
</footer>

</body>
</html>
```